I will ask the design of the business card

We are looking for business card design of the new company "R DOVE PAYGRID WORKS LLC." Based in Azerbaijan.
In case
We are working on Azerbaijan to set up the first exchange of crypto currencies.

The key currency used in exchanges is called "PLUME".
In case
We are doing project to make crypto currency infrastructure.

We provide state-of-the-art technology to the world.

```html
<!DOCTYPE html>
<html lang="en">
<head>
<meta charset="utf-8">
<title>Dove Paygrid Works LLC – Business Card</title>
<link href="https://fonts.googleapis.com/css2?family=Work+Sans:wght@400;500&family=Poppins:wght@400&display=swap" rel="stylesheet">
<style>
  :root{
    --backdrop:#6e5840;
    --card-light:#ffffff;
    --card-dark:#323232;
    --brand-blue:#1a6fba;
    --ink:#333333;
    --ink-soft:#3d3d3d;
    --on-dark:#ffffff;
  }
  *{margin:0;padding:0;box-sizing:border-box}
  html,body{width:1200px;height:930px;overflow:hidden}
  body{background:var(--backdrop);position:relative;font-family:"Work Sans",sans-serif;color:var(--ink)}
  .card{position:absolute;border-radius:22px;box-shadow:0 6px 18px rgba(0,0,0,.35)}
  .card-front{left:278px;top:75px;width:644px;height:369px;background:var(--card-light)}
  .card-back{left:278px;top:486px;width:646px;height:368px;background:var(--card-dark);display:flex;align-items:center;justify-content:center}

  .contact{position:absolute;right:358px;text-align:right;white-space:nowrap}
  .person-name{top:97px;font-size:27px;font-weight:500;letter-spacing:1.5px;color:var(--brand-blue);line-height:1}
  .person-role{top:126px;font-size:16px;line-height:1;color:var(--ink)}
  .address{top:160px;font-size:16px;line-height:21px;color:var(--ink-soft)}
  .channels{top:216px;right:358px;font-size:16px;line-height:20.5px;color:var(--ink-soft)}
  .channels li{list-style:none;display:flex;justify-content:flex-end;align-items:center;gap:12px}
  .channels svg{width:10px;height:10px;flex:none}
  .channels .link{color:var(--brand-blue)}

  .divider{position:absolute;left:313px;width:2px;background:var(--brand-blue)}
  .divider-top{top:103px;height:38px}
  .divider-bottom{top:163px;height:109px}

  .brand{display:flex;align-items:center;font-family:"Poppins",sans-serif;font-weight:400;white-space:nowrap}
  .brand-dot{border-radius:50%;background:var(--brand-blue);flex:none}
  .brand-front{position:absolute;left:339px;top:174px;font-size:18px;color:var(--ink)}
  .brand-front .brand-dot{width:26px;height:26px;margin-right:10px}
  .brand-back{font-size:30px;color:var(--on-dark)}
  .brand-back .brand-dot{width:46px;height:46px;margin-right:16px}
</style>
</head>
<body>
  <section class="card card-front">
    <h1 class="contact person-name">DANIEL HARLOW</h1>
    <p class="contact person-role">Director</p>
    <p class="contact address">AZ1000 , 8/3A. Nizami str.<br>Baku city, Azerbaijan</p>
    <ul class="contact channels">
      <li>615-555-0142
        <svg viewBox="0 0 10 10"><path d="M2 1 L3.5 1 L4 3 L3 3.8 Q4 6 6.2 7 L7 6 L9 6.5 L9 8 Q8.5 9 7.5 9 Q2 8 1 2.5 Q1 1.3 2 1Z" fill="#1a6fba"/></svg></li>
      <li>support@plume.technology
        <svg viewBox="0 0 10 10"><rect x="0.8" y="2" width="8.4" height="6" rx="1" fill="none" stroke="#1a6fba" stroke-width="1.2"/><path d="M1 2.5 L5 5.5 L9 2.5" fill="none" stroke="#1a6fba" stroke-width="1.1"/></svg></li>
      <li><span>www.<span class="link">guild.plume.technology</span></span>
        <svg viewBox="0 0 10 10"><circle cx="5" cy="5" r="4.2" fill="none" stroke="#1a6fba" stroke-width="1"/><ellipse cx="5" cy="5" rx="1.8" ry="4.2" fill="none" stroke="#1a6fba" stroke-width=".8"/><path d="M0.8 5 H9.2 M1.5 3 H8.5 M1.5 7 H8.5" stroke="#1a6fba" stroke-width=".7"/></svg></li>
    </ul>
    <span class="divider divider-top"></span>
    <span class="divider divider-bottom"></span>
    <div class="brand brand-front"><span class="brand-dot"></span>DOVE PAYGRID WORKS LLC</div>
  </section>

  <section class="card card-back">
    <div class="brand brand-back"><span class="brand-dot"></span>DOVE PAYGRID WORKS LLC</div>
  </section>
</body>
</html>
```